Mental Health care Company in Washington DC

We are a new mental health care services provider in Washington DC. Please look at these sites.
https://brightwaterfamilysupport.com
https://www.quietharborinc.com
https://willowgate-dc.org/
https://www.tidepathdc.com
https://www.thelanternofdc.com

```html
<!DOCTYPE html>
<html lang="en">
<head>
<meta charset="utf-8">
<title>Calder Health Services</title>
<link href="https://fonts.googleapis.com/css2?family=Outfit:wght@400;500;600&family=Open+Sans:wght@400;600&display=swap" rel="stylesheet">
<style>
:root{
  --navy:#0b1033;
  --ink:#0f1a3d;
  --orange:#f37f20;
  --teal:#a3d9dc;
  --teal-deep:#8fcfd3;
  --sky:#e2f6f8;
  --mist:#f4f8f9;
  --news:#1f2b57;
  --text:#4a4f60;
  --white:#ffffff;
}
*{box-sizing:border-box;margin:0;padding:0}
html,body{width:1200px;height:3779px;overflow:hidden}
body{font-family:"Open Sans",Arial,sans-serif;color:var(--text);background:var(--white);position:relative}
h1,h2,h3,.brand,.nav a,.btn{font-family:"Outfit",Arial,sans-serif}
.abs{position:absolute}
.photo{position:absolute;overflow:hidden}
.btn{position:absolute;display:flex;align-items:center;justify-content:center;background:var(--orange);color:var(--white);font-weight:500;font-size:15px;border-radius:26px 0 26px 0;text-decoration:none}

/* top bar */
.topbar{position:absolute;left:0;top:0;width:1200px;height:35px;background:var(--navy);color:var(--white);font-size:12.5px}
.topbar span{position:absolute;top:9px;display:flex;align-items:center;gap:8px}

/* header + hero */
.hero{position:absolute;left:0;top:35px;width:1200px;height:603px;background:linear-gradient(160deg,#f8fafb 0%,#eef7f8 55%,#dff3f5 100%)}
.brand{font-size:34px;font-weight:500;color:var(--ink);letter-spacing:-.5px}
.nav{position:absolute;left:392px;top:26px;display:flex;gap:30px;font-size:15px}
.nav a{color:var(--ink);text-decoration:none}
.nav a.active{color:var(--orange)}
.hero h1{position:absolute;left:144px;top:180px;font-size:41px;line-height:48px;font-weight:500;color:var(--ink)}
.hero p{position:absolute;left:144px;top:287px;width:420px;font-size:14.5px;line-height:24px}
.dots{position:absolute;left:144px;top:536px;display:flex;gap:7px}
.dots i{width:11px;height:11px;border-radius:50%;background:#d5d9de;display:block}
.dots i:first-child{background:var(--orange)}

/* band */
.band{position:absolute;left:0;top:638px;width:1200px;height:176px;background:var(--teal)}
.band h2{position:absolute;left:144px;top:40px;font-size:32px;font-weight:500;color:var(--white)}
.band p{position:absolute;left:144px;top:86px;width:580px;font-size:14.5px;line-height:24px;color:var(--white)}

/* services */
.section-title{position:absolute;left:0;width:1200px;text-align:center;font-size:41px;font-weight:500;color:var(--ink)}
.card{position:absolute;top:973px;width:212px;height:337px;background:var(--white);border-radius:10px;box-shadow:0 4px 14px rgba(15,26,61,.08);overflow:hidden}
.card .photo{left:0;top:0;width:212px;height:176px}
.card h3{position:absolute;left:18px;top:190px;width:150px;font-size:15.5px;line-height:24px;font-weight:600;color:var(--ink);z-index:1}
.card .num{position:absolute;right:12px;top:186px;font-family:"Outfit",Arial,sans-serif;font-size:44px;font-weight:600;color:#eceef2}
.card p{position:absolute;left:18px;top:252px;width:180px;font-size:12.5px;line-height:20px}
.card.featured{background:var(--orange)}
.card.featured h3,.card.featured p{color:var(--white)}
.card.featured h3{text-decoration:underline}
.card.featured .num{color:rgba(255,255,255,.2)}

/* welcome */
.welcome{position:absolute;left:0;top:1416px;width:1200px;height:718px;background:linear-gradient(180deg,var(--sky),#eaf8fa)}
.welcome p.lead{position:absolute;left:228px;top:189px;width:744px;text-align:center;font-size:14px;line-height:24px}
.tile{position:absolute;top:296px;width:441px;height:305px;border-radius:70px 0 0 0;overflow:hidden}
.tile .label{position:absolute;left:44px;bottom:34px;font-family:"Outfit",Arial,sans-serif;font-size:20px;font-weight:500;color:var(--white)}
.tile .go{position:absolute;right:0;bottom:0;width:64px;height:64px;background:var(--orange);border-radius:40px 0 0 0;display:flex;align-items:center;justify-content:center}

/* care team */
.care h2{position:absolute;left:626px;top:2247px;font-size:41px;font-weight:500;color:var(--ink)}
.care p{position:absolute;left:626px;top:2308px;width:420px;font-size:13.5px;line-height:21.6px}

/* newsletter */
.newsletter{position:absolute;left:0;top:2714px;width:1200px;height:363px;background:linear-gradient(90deg,var(--news) 0%,#26335f 60%,#2e3a63 100%)}
.newsletter h2{position:absolute;left:144px;top:100px;font-size:41px;font-weight:500;color:var(--white)}
.newsletter p{position:absolute;left:144px;top:162px;font-size:15px;color:var(--white)}
.field{position:absolute;top:202px;height:52px;background:var(--white);border-radius:26px 0 26px 0;font-size:14.5px;color:#6a6f7d;padding-left:40px;display:flex;align-items:center}

/* contact */
.contact-col{position:absolute;top:3259px;width:300px;text-align:center}
.contact-col .ico{width:58px;height:58px;border-radius:50%;background:var(--orange);margin:0 auto;display:flex;align-items:center;justify-content:center}
.contact-col h3{margin-top:22px;font-size:26px;font-weight:500;color:var(--ink)}
.contact-col p{margin-top:6px;font-size:14px;line-height:24px;color:var(--ink)}
.divider{position:absolute;top:3257px;width:1px;height:146px;background:#d3d6dc}

/* footer */
.footer{position:absolute;left:0;top:3487px;width:1200px;height:292px;background:linear-gradient(180deg,#e0f4f5,#d6eff1)}
.footer .rule{position:absolute;left:0;top:200px;width:1200px;height:1px;background:#bcd9dc}
.flink{position:absolute;font-family:"Outfit",Arial,sans-serif;font-size:19px;color:var(--ink);display:flex;align-items:center;gap:22px}
.flink b{color:var(--orange);font-weight:400;font-size:16px}
.copy{position:absolute;left:0;top:236px;width:1200px;text-align:center;font-size:15px;color:var(--ink)}
</style>
</head>
<body>

<div class="topbar">
  <span style="left:144px">
    <svg width="12" height="12" viewBox="0 0 12 12"><circle cx="6" cy="6" r="5" fill="none" stroke="#f37f20" stroke-width="1.6"/><path d="M6 3v3h2" stroke="#f37f20" stroke-width="1.4" fill="none"/></svg>
    Hours: M-F 8:30 a.m. - 5:00 p.m.
  </span>
  <span style="left:884px">
    <svg width="12" height="12" viewBox="0 0 24 24"><path fill="#f37f20" d="M6.6 10.8a15.1 15.1 0 0 0 6.6 6.6l2.2-2.2c.3-.3.7-.4 1-.2 1.1.4 2.3.6 3.6.6.6 0 1 .4 1 1V20c0 .6-.4 1-1 1A17 17 0 0 1 3 4c0-.6.4-1 1-1h3.5c.6 0 1 .4 1 1 0 1.3.2 2.5.6 3.6.1.3 0 .7-.2 1z"/></svg>
    Call Us : +1 888 888 8888
  </span>
</div>

<header class="hero">
  <div class="brand abs" style="left:144px;top:16px">Calder Health</div>
  <nav class="nav">
    <a class="active" href="#">Home</a><a href="#">Our Services</a><a href="#">Insurance</a><a href="#">About</a><a href="#">Contact</a>
  </nav>
  <a class="btn" href="#" style="left:836px;top:16px;width:220px;height:44px">Make an Appointment</a>

  <h1>Care You Can Trust.<br>Support You Deserve.</h1>
  <p>Lorem ipsum dolor sit amet, consectetur adipiscing elit, incididunt ut labore et dolore magna aliqua.</p>
  <a class="btn" href="#" style="left:144px;top:352px;width:222px;height:44px">Make an Appointment</a>
  <div class="dots"><i></i><i></i><i></i><i></i></div>

  <div class="photo" role="img" aria-label="Therapist listening to a client in a bright office" style="left:678px;top:143px;width:189px;height:189px;border-radius:0 90px 0 40px;background:linear-gradient(135deg,#c8c4b4,#7e8a84)"></div>
  <div class="photo" role="img" aria-label="Counselor shaking hands with a client" style="left:927px;top:79px;width:273px;height:275px;border-radius:0 0 0 180px;background:linear-gradient(135deg,#e6e3dc,#9aa6a8)"></div>
  <div class="abs" style="left:877px;top:343px;width:77px;height:78px;background:var(--teal);border-radius:0 0 0 40px"></div>
  <div class="photo" role="img" aria-label="Two women talking in a counseling session" style="left:634px;top:402px;width:251px;height:201px;border-radius:0 90px 0 0;background:linear-gradient(135deg,#8a6c5c,#4d4a52)"></div>
  <div class="photo" role="img" aria-label="Smiling family embracing" style="left:954px;top:402px;width:173px;height:173px;border-radius:50%;background:linear-gradient(135deg,#9fb2c4,#33486a)"></div>
</header>

<section class="band">
  <h2>Empowering Communities for Better Life</h2>
  <p>Lorem ipsum dolor sit amet, consectetur adipiscing elit, sed do eiusmod tempor incididunt ut labore et dolore magna aliqua.</p>
  <a class="btn" href="#" style="left:836px;top:69px;width:220px;height:41px">Learn More About Us</a>
</section>

<section class="services">
  <h2 class="section-title" style="top:908px">Services We Offer</h2>
  <svg class="abs" style="left:58px;top:1124px" width="28" height="46" viewBox="0 0 28 46"><path d="M24 2 4 23l20 21" fill="none" stroke="#0f1a3d" stroke-width="2.4"/></svg>
  <svg class="abs" style="left:1114px;top:1124px" width="28" height="46" viewBox="0 0 28 46"><path d="M4 2l20 21L4 44" fill="none" stroke="#0f1a3d" stroke-width="2.4"/></svg>

  <article class="card" style="left:144px">
    <div class="photo" role="img" aria-label="Therapist in session with a woman on a sofa" style="background:linear-gradient(135deg,#e3ded6,#9e8f84)"></div>
    <span class="num">01</span><h3>Individual<br>Therapy</h3>
    <p>Lorem ipsum dolor sit amet, consectetur adipiscing elit, sed do eiusmod</p>
  </article>
  <article class="card featured" style="left:377px">
    <div class="photo" role="img" aria-label="Clinician discussing medication with a young man" style="background:linear-gradient(135deg,#c9a27c,#6b4e3c)"></div>
    <span class="num">02</span><h3>Medication<br>Management</h3>
    <p>Lorem ipsum dolor sit amet, consectetur adipiscing elit, sed do eiusmod</p>
  </article>
  <article class="card" style="left:610px">
    <div class="photo" role="img" aria-label="Psychiatrist taking notes during a consultation" style="background:linear-gradient(135deg,#7d8a86,#3d4446)"></div>
    <span class="num">03</span><h3>Psychiatry</h3>
    <p>Lorem ipsum dolor sit amet, consectetur adipiscing elit, sed do eiusmod</p>
  </article>
  <article class="card" style="left:843px">
    <div class="photo" role="img" aria-label="Support worker meeting a client in a lounge" style="background:linear-gradient(135deg,#d4d0c8,#4b5258)"></div>
    <span class="num">04</span><h3>Community<br>Support Services</h3>
    <p>Lorem ipsum dolor sit amet, consectetur adipiscing elit, sed do eiusmod</p>
  </article>
</section>

<section class="welcome">
  <h2 class="section-title" style="top:118px">Welcome To Calder Health</h2>
  <p class="lead">Lorem ipsum dolor sit amet, consectetur adipiscing elit, sed do eiusmod tempor incididunt ut labore et dolore magna aliqua. Ut enim ad minim veniam, quis nostrud exercitation ullamco laboris nisi ut aliquip ex ea commodo consequat. Duis aute irure dolor in reprehenderit in voluptate velit esse cillum dolore eu fugiat nulla pariatur. Excepteur sint occaecat cupidatat non proident, sunt in culpa qui officia deserunt mollit anim id est laborum.</p>
  <div class="tile" role="img" aria-label="Family meeting with a counselor" style="left:144px;background:linear-gradient(135deg,#a89888,#3a3432)">
    <span class="label">Media Public Relations</span>
    <span class="go"><svg width="22" height="22" viewBox="0 0 22 22"><path d="M5 17 17 5M8 5h9v9" fill="none" stroke="#fff" stroke-width="2.2"/></svg></span>
  </div>
  <div class="tile" role="img" aria-label="Couple talking on a sofa" style="left:614px;background:linear-gradient(135deg,#b7c3c6,#4a4440)">
    <span class="label">Employment Opportunity</span>
    <span class="go"><svg width="22" height="22" viewBox="0 0 22 22"><path d="M5 17 17 5M8 5h9v9" fill="none" stroke="#fff" stroke-width="2.2"/></svg></span>
  </div>
</section>

<section class="care">
  <div class="photo" role="img" aria-label="Parents and child laughing together" style="left:0;top:2343px;width:320px;height:290px;border-radius:0 90px 0 0;background:linear-gradient(135deg,#e6d4c2,#9a7258)"></div>
  <div class="photo" role="img" aria-label="Counselor talking with a man" style="left:340px;top:2220px;width:204px;height:203px;border-radius:0 100px 0 0;background:linear-gradient(135deg,#c7ccc2,#5d6a5a)"></div>
  <div class="abs" style="left:355px;top:2463px;width:103px;height:103px;background:var(--teal);border-radius:0 0 0 50px"></div>
  <h2>Your Care Team</h2>
  <p>Lorem ipsum dolor sit amet, consectetur adipiscing elit, sed do eiusmod tempor incididunt ut labore et dolore magna aliqua. Ut enim ad minim veniam, quis nostrud exercitation ullamco laboris nisi ut aliquip ex ea commodo consequat. Duis aute irure dolor in reprehenderit in voluptate velit esse cillum dolore eu fugiat nulla pariatur. Excepteur sint occaecat cupidatat non proident, sunt in culpa qui officia deserunt mollit anim id est laborum. Lorem ipsum dolor sit amet, consectetur adipiscing elit, sed do eiusmod tempor incididunt ut labore et dolore magna aliqua. Ut enim ad minim veniam, quis nostrud exercitation ullamco laboris nisi ut aliquip ex ea commodo consequat.</p>
  <a class="btn" href="#" style="left:626px;top:2563px;width:222px;height:44px">Learn More About Us</a>
</section>

<section class="newsletter" role="img" aria-label="Newsletter banner over a dim navy photo of a smiling woman">
  <h2>Calder Health Newsletter</h2>
  <p>Subscribe to our newsletter to receive regular news and updates about the company.</p>
  <div class="field" style="left:144px;width:349px">Full name</div>
  <div class="field" style="left:505px;width:340px">Email address</div>
  <a class="btn" href="#" style="left:858px;top:202px;width:198px;height:52px;font-size:18px">Subscribe</a>
</section>

<section class="contact">
  <h2 class="section-title" style="top:3174px">Contact Details</h2>
  <div class="contact-col" style="left:145px">
    <div class="ico"><svg width="18" height="22" viewBox="0 0 18 22"><path d="M9 1a7 7 0 0 0-7 7c0 5 7 13 7 13s7-8 7-13a7 7 0 0 0-7-7z" fill="#fff"/><circle cx="9" cy="8" r="2.6" fill="#f37f20"/></svg></div>
    <h3>Address</h3><p>123, Lorem ipsum dolor<br>Washington DC</p>
  </div>
  <div class="divider" style="left:443px"></div>
  <div class="contact-col" style="left:450px">
    <div class="ico"><svg width="20" height="16" viewBox="0 0 20 16"><rect x="1" y="1" width="18" height="14" rx="2" fill="#fff"/><path d="M2 3l8 6 8-6" fill="none" stroke="#f37f20" stroke-width="1.6"/></svg></div>
    <h3>Email Address</h3><p>info@companyname.com</p>
  </div>
  <div class="divider" style="left:763px"></div>
  <div class="contact-col" style="left:754px">
    <div class="ico"><svg width="20" height="20" viewBox="0 0 24 24"><path fill="#fff" d="M6.6 10.8a15.1 15.1 0 0 0 6.6 6.6l2.2-2.2c.3-.3.7-.4 1-.2 1.1.4 2.3.6 3.6.6.6 0 1 .4 1 1V20c0 .6-.4 1-1 1A17 17 0 0 1 3 4c0-.6.4-1 1-1h3.5c.6 0 1 .4 1 1 0 1.3.2 2.5.6 3.6.1.3 0 .7-.2 1z"/></svg></div>
    <h3>Phone</h3><p>+1 888 888 8888</p>
  </div>
</section>

<footer class="footer">
  <div class="brand abs" style="left:144px;top:84px;font-size:46px">Calder Health</div>
  <a class="flink" style="left:490px;top:76px"><b>»</b>Home</a>
  <a class="flink" style="left:490px;top:125px"><b>»</b>About Us</a>
  <a class="flink" style="left:682px;top:76px"><b>»</b>Services</a>
  <a class="flink" style="left:682px;top:125px"><b>»</b>Careers</a>
  <a class="flink" style="left:882px;top:76px"><b>»</b>Contact Us</a>
  <a class="flink" style="left:882px;top:125px"><b>»</b>Privacy Policy</a>
  <div class="rule"></div>
  <div class="copy">© Copyrights 2025 | All Rights Reserved</div>
</footer>

</body>
</html>
```